Disposable Mini Sauce Pot Design for Asian Chain Food Brands

We operate a Hainan Chicken Rice takeout brand under the name Brindle4U, with our official website: www.Brindle4U.example.
We offer four signature house sauces and are launching brand-new packaging for our sauce line. We require custom graphic designs exclusively for the sauce cup lids.
Product Material & Base Specs
The sauce cups are made of PP plastic, available in two translucent base options: Translucent White and Translucent Orange.
Four Sauce Varieties for Individual Lid Designs
1. Red Sauce – Fried Sweet Chili Sauce
2.Green Sauce – Scallion Oil Dressing
3.Sweet Soy Sauce
4.Sweet Red Sauce (Special for Fried Chicken)
Differentiate each sauce lid design through unique graphics, typography, or illustrative elements for easy customer identification.
The marking NET WT 2 OZ must be clearly printed on every lid.
**There is no need to print full descriptive text or the full name of the sauces on each lid; the design only needs to clearly differentiate the four sauce varieties.
**Please reference the original design style and brand color palette shown on our official website, and feel free to fully unleash your creativity.
Look and feel
Each slider illustrates characteristics of the customer's brand and the style your logo design should communicate.

```html
<!DOCTYPE html>
<html lang="en">
<head>
<meta charset="utf-8">
<title>Brindle4U Sauce Lids</title>
<link rel="stylesheet" href="https://fonts.googleapis.com/css2?family=Montserrat:wght@800;900&display=swap">
<style>
  :root {
    --page: #fafafa;
    --red: #e3140d;
    --green: #6aac2b;
    --soy: #322a85;
    --pink: #e43f6a;
    --splat: #8a0d22;
    --ink: #ffffff;
  }
  html, body {
    margin: 0;
    padding: 0;
    overflow: hidden;
    background: var(--page);
  }
  .sheet {
    position: relative;
    width: 1072px;
    height: 1200px;
    background: var(--page);
    overflow: hidden;
  }
  .lid {
    position: absolute;
    width: 455px;
    height: 516px;
  }
  .lid--red { left: 69px; top: 84px; }
  .lid--green { left: 548px; top: 84px; }
  .lid--soy { left: 69px; top: 624px; }
  .lid--sweet-red { left: 548px; top: 624px; }
  .lid text {
    font-family: "Montserrat", sans-serif;
    font-weight: 900;
    fill: var(--ink);
  }
  .lid .net-wt, .lid .brand {
    font-weight: 800;
  }
  .base--red { fill: var(--red); }
  .base--green { fill: var(--green); }
  .base--soy { fill: var(--soy); }
  .base--pink { fill: var(--pink); }
  .splat { fill: var(--splat); }
</style>
</head>
<body>
<main class="sheet">

  <svg class="lid lid--red" viewBox="0 0 774 876" aria-label="Red sauce lid">
    <rect class="base--red" width="774" height="876" rx="130"/>
    <ellipse class="splat" cx="360" cy="620" rx="230" ry="160" role="img" aria-label="Sauce splash illustration"/>
    <text x="90" y="554" font-size="640" textLength="405" lengthAdjust="spacingAndGlyphs">R</text>
    <text x="573" y="325" font-size="305" textLength="100" lengthAdjust="spacingAndGlyphs">E</text>
    <text x="573" y="560" font-size="305" textLength="150" lengthAdjust="spacingAndGlyphs">D</text>
    <text x="76" y="687" font-size="230" textLength="632" lengthAdjust="spacingAndGlyphs">sauce</text>
    <text class="net-wt" x="35" y="803" font-size="30">NET WT 2 OZ</text>
    <text class="brand" x="745" y="803" font-size="38" text-anchor="end">Brindle4U</text>
  </svg>

  <svg class="lid lid--green" viewBox="0 0 774 876" aria-label="Green sauce lid">
    <rect class="base--green" width="774" height="876" rx="130"/>
    <ellipse class="splat" cx="360" cy="630" rx="220" ry="165" role="img" aria-label="Sauce splash illustration"/>
    <text x="105" y="375" font-size="425" textLength="565" lengthAdjust="spacingAndGlyphs">GR</text>
    <text x="120" y="587" font-size="296" textLength="552" lengthAdjust="spacingAndGlyphs">EEN</text>
    <text x="120" y="700" font-size="200" textLength="552" lengthAdjust="spacingAndGlyphs">sauce</text>
    <text class="net-wt" x="35" y="803" font-size="30">NET WT 2 OZ</text>
    <text class="brand" x="745" y="803" font-size="38" text-anchor="end">Brindle4U</text>
  </svg>

  <svg class="lid lid--soy" viewBox="0 0 774 876" aria-label="Sweet soy sauce lid">
    <rect class="base--soy" width="774" height="876" rx="130"/>
    <ellipse class="splat" cx="355" cy="600" rx="225" ry="185" role="img" aria-label="Sauce splash illustration"/>
    <text x="123" y="278" font-size="297" textLength="532" lengthAdjust="spacingAndGlyphs">SW</text>
    <text x="116" y="485" font-size="280" textLength="527" lengthAdjust="spacingAndGlyphs">eet</text>
    <text x="123" y="665" font-size="245" textLength="520" lengthAdjust="spacingAndGlyphs">SOY</text>
    <text x="258" y="730" font-size="100" textLength="257" lengthAdjust="spacingAndGlyphs">sauce</text>
    <text class="net-wt" x="35" y="803" font-size="30">NET WT 2 OZ</text>
    <text class="brand" x="745" y="803" font-size="38" text-anchor="end">Brindle4U</text>
  </svg>

  <svg class="lid lid--sweet-red" viewBox="0 0 774 876" aria-label="Sweet red sauce lid">
    <rect class="base--pink" width="774" height="876" rx="130"/>
    <ellipse class="splat" cx="355" cy="600" rx="225" ry="185" role="img" aria-label="Sauce splash illustration"/>
    <text x="120" y="278" font-size="297" textLength="535" lengthAdjust="spacingAndGlyphs">SW</text>
    <text x="117" y="485" font-size="280" textLength="525" lengthAdjust="spacingAndGlyphs">eet</text>
    <text x="142" y="665" font-size="245" textLength="506" lengthAdjust="spacingAndGlyphs">RED</text>
    <text x="258" y="730" font-size="100" textLength="259" lengthAdjust="spacingAndGlyphs">sauce</text>
    <text class="net-wt" x="35" y="803" font-size="30">NET WT 2 OZ</text>
    <text class="brand" x="745" y="803" font-size="38" text-anchor="end">Brindle4U</text>
  </svg>

</main>
</body>
</html>
```